Personal Chef Needs a Good Web Design

Hi everyone!
My name is Leo, I work as a private chef for last 10 years, traveling all around the world and cooking in private megayacht and villas.
I'm about to settle down in my hometown in Europe for a while. And therefore I need a website that will show my story, pics and recipes, nutritional advices and of course offer a Personal and Private Chef services( working for 4-5 families and bringing delicious food to their house).
My clients are extremely rich folks, but usually are down to earth ones.
I believe, the web site should be focused on attention to:
-VIP person's wife( as she is usually responsible for food for family) and be simple.
-to famous people agents and be on high level.

There will be about 10 different menus and 6 different service offers

--UPDATE--
Logo Design:
+My thoughts are- printed structure of the vegetable or fruit on a white font. Like you slice the buffalo tomato, put it in red paint and print it on the edge of the page. See attached files named logo. Can be any nice structured thing, like tomato, lemon, red cabbage etc.
+Classic logos with chef's hat or knives are good too.
+Need to have the space for me to add the name( the fonts can be provided)

Target Market(s)

Private person. 80% Russian clients.

Industry/Entity Type

Cooking

Coding

Coded - Design and coding required

Number of Pages Required

3 page

Requirements
Must have
• Contact form/ Request back call/ Schedule a free consultation
Nice to have
• The client will need to choose straight ahead from the range of services I offer, like:
• -Private Chef( cooking only for the client)
• -Personal Chef( cooking for around 5 clients, bringing the ready to be heated food to their door)
• -Romantic dinner for two
• -Professional Sommelier service
• -Build your kitchen( offering design, equipment and that will fit your requirements)
• -Other( flowers, waiters, barista, equipment rental)
• So this column should go right after the introduction/aboutme part and will lead to separate pages with how-it-works thing for each.

```html
<!DOCTYPE html>
<html lang="en">
<head>
<meta charset="utf-8">
<title>Leo Chef</title>
<link rel="stylesheet" href="https://fonts.googleapis.com/css2?family=Montserrat:wght@500;600&family=Open+Sans:wght@400;600;700&display=swap">
<style>
:root{
  --orange:#d9954a;
  --ink:#1f1f1f;
  --text:#666666;
  --line:#cfcfcf;
  --white:#ffffff;
  --photo-chef:linear-gradient(160deg,#8a8f94,#d9d6d0 45%,#6b5a48);
  --photo-salad:linear-gradient(120deg,#c9c3b8,#5d7a3a 45%,#b8432d 75%,#e1c08a);
  --photo-board:linear-gradient(135deg,#7d8a8c,#b65a3e 50%,#d2a75a);
  --photo-flame:linear-gradient(150deg,#2b1d14,#d2692a 50%,#f2b441 70%,#3a2a22);
}
*{margin:0;padding:0;box-sizing:border-box}
html,body{width:715px;height:1200px;overflow:hidden;background:var(--white)}
body{position:relative;font-family:"Open Sans",Arial,sans-serif;color:var(--text);font-size:7.5px}
.abs{position:absolute}
.heading{font-family:"Montserrat",Arial,sans-serif;font-weight:500;color:var(--ink);letter-spacing:.2px}
.site-header{left:0;top:0;width:715px;height:48px;border-bottom:1px solid var(--line)}
.brand{left:58px;top:17px;font-size:13.5px;font-family:"Open Sans",Arial,sans-serif;font-weight:600;color:var(--ink)}
.menu-toggle{left:635px;top:14px}
.framed-photo{border:1px solid #9a9a9a;padding:3px;background:var(--white)}
.framed-photo .photo{width:100%;height:100%}
.about-photo{left:58px;top:81px;width:206px;height:243px}
.about-title{left:297px;top:85px;font-size:18px}
.about-text{left:299px;top:114px;width:360px;line-height:19px}
.about-text p+p{margin-top:19px}
.btn{display:block;text-align:center;font-weight:700;font-size:7px;letter-spacing:.2px}
.btn-solid{background:var(--orange);color:var(--white)}
.btn-outline{border:1px solid var(--white);color:var(--white)}
.about-btn{left:299px;top:301px;width:71px;height:20px;line-height:20px}
.benefits-photo{left:0;top:358px;width:358px;height:237px}
.benefits-panel{left:358px;top:358px;width:357px;height:237px;background:var(--orange);color:var(--white)}
.benefits-title{left:39px;top:28px;font-size:17px;color:var(--white)}
.benefits-text{left:40px;top:58px;width:280px;line-height:15px;font-size:7.2px}
.benefit-list{left:40px;top:99px;list-style:none;font-size:7.2px}
.benefit-list li{height:21.5px;display:flex;align-items:center;gap:7px}
.benefits-btn{left:40px;top:193px;width:72px;height:21px;line-height:19px}
.works-title{left:0;top:632px;width:715px;text-align:center;font-size:18px}
.work-photo{width:106px;height:90px;top:681px}
.work-photo.first{left:58px}
.work-photo.second{left:377px}
.work-text{top:678px;width:165px;line-height:16.4px;font-size:7.2px}
.work-text.first{left:178px}
.work-text.second{left:498px}
.divider{left:58px;top:851px;width:600px;height:1px;background:var(--line)}
.accent-band{left:0;top:863px;width:715px;height:3px;background:var(--orange)}
.contact-title{left:0;top:888px;width:715px;text-align:center;font-size:18px}
.sub-title{font-family:"Open Sans",Arial,sans-serif;font-weight:600;font-size:9px;color:var(--ink)}
.form-title{left:58px;top:936px}
.field-label{font-size:6.8px;color:var(--text)}
.field{border:1px solid #a9a9a9;background:var(--white)}
.submit{left:382px;top:1110px;width:52px;height:21px;line-height:21px;font-size:8.5px;font-family:"Open Sans",Arial,sans-serif}
.info-title{left:482px;top:936px}
.info-row{left:483px;display:flex;align-items:center;gap:14px;font-size:7px}
.info-row .lines{line-height:14px}
.hours-title{left:482px;top:1069px}
.hours{left:482px;top:1088px;font-size:7px;line-height:15.5px;border-collapse:collapse}
.hours td{padding:0}
.hours td.day{width:85px}
.footer-line{left:58px;top:1154px;width:600px;height:1px;background:var(--line)}
.copyright{left:58px;top:1171px;font-size:7px}
.social{left:568px;top:1168px;display:flex;gap:9px}
.social span{width:15px;height:15px;border-radius:3px;background:#8c8c8c;display:block}
</style>
</head>
<body>

<header class="abs site-header">
  <div class="abs brand">LEO CHEF</div>
  <svg class="abs menu-toggle" width="22" height="22" viewBox="0 0 22 22" aria-label="Menu">
    <circle cx="11" cy="11" r="10.3" fill="none" stroke="#8c8c8c" stroke-width="0.8"/>
    <path d="M7 8h8M7 11h8M7 14h8" stroke="#d9954a" stroke-width="1.6" stroke-linecap="round"/>
  </svg>
</header>

<section class="about">
  <div class="abs framed-photo about-photo">
    <div class="photo" role="img" aria-label="Portrait of the chef in white jacket, arms crossed, in a bakery kitchen" style="background:var(--photo-chef)"></div>
  </div>
  <h1 class="abs heading about-title">PRIVATE CHEF</h1>
  <div class="abs about-text">
    <p>At vero eos et accusamus et iusto odio dignissimos ducimus qui blanditiis praesentium voluptatum deleniti at que corrupti quos dolores et quas molestias excepturi.</p>
    <p>Sint occaecati cupiditate non provident, similique sunt in culpa qui officia deserunt mollitia animi, id est lab orum et dolorum fuga. Et harum quidem rerum facilis est et expedita distinctio. Nam libero tempore, cum soluta nobis est eligendi optio cumque nihil impedit quo minus id quod maxime placeat facere possimum nis voluptas assumenda est, omnis dolor repellendus. Temporibus autem quibusdam et aut officiis debitis aut rerum necessitatibus saepe eveniet ut et voluptates. Et harum quidem rerum facilis est et expedita dist inctio. Nam libero tempore, cum eligendi optio cumque nihil impe.</p>
  </div>
  <a class="abs btn btn-solid about-btn">READ MORE &gt;&gt;</a>
</section>

<section class="benefits">
  <div class="abs benefits-photo" role="img" aria-label="Chef tossing a fresh salad over a counter of vegetables" style="background:var(--photo-salad)"></div>
  <div class="abs benefits-panel">
    <h2 class="abs heading benefits-title">BENEFITS</h2>
    <p class="abs benefits-text">At vero eos et accusamus et iusto odio dignissimos ducimus qui blanditiis praesen tium voluptatum deleniti atque corrupti quoscaecati.</p>
    <ul class="abs benefit-list">
      <li><svg width="8" height="8" viewBox="0 0 8 8"><circle cx="4" cy="4" r="4" fill="#fff"/><path d="M2.2 4.1l1.2 1.2 2.4-2.5" fill="none" stroke="#d9954a" stroke-width="1"/></svg>Nam libero tempore, cum soluta nobis est eligendi optio ostru</li>
      <li><svg width="8" height="8" viewBox="0 0 8 8"><circle cx="4" cy="4" r="4" fill="#fff"/><path d="M2.2 4.1l1.2 1.2 2.4-2.5" fill="none" stroke="#d9954a" stroke-width="1"/></svg>Debitis aut rerum necessitatibus saepe eveniet ut et volupsitat</li>
      <li><svg width="8" height="8" viewBox="0 0 8 8"><circle cx="4" cy="4" r="4" fill="#fff"/><path d="M2.2 4.1l1.2 1.2 2.4-2.5" fill="none" stroke="#d9954a" stroke-width="1"/></svg>Ut aut reiciendis voluptatibus maiores alias consequatur volup</li>
      <li><svg width="8" height="8" viewBox="0 0 8 8"><circle cx="4" cy="4" r="4" fill="#fff"/><path d="M2.2 4.1l1.2 1.2 2.4-2.5" fill="none" stroke="#d9954a" stroke-width="1"/></svg>Ut enim ad minima veniam, quis nostrum exercitationem uluis</li>
    </ul>
    <a class="abs btn btn-outline benefits-btn">READ MORE &gt;&gt;</a>
  </div>
</section>

<section class="how-it-works">
  <h2 class="abs heading works-title">HOW IT WORKS</h2>
  <div class="abs framed-photo work-photo first">
    <div class="photo" role="img" aria-label="Hands slicing tomatoes on a wooden board" style="background:var(--photo-board)"></div>
  </div>
  <p class="abs work-text first">Our first consultation will be in your home. We will discuss any food preferences you may have, as well as any allergy or dietary needs. At this time we will also discus what kind of meals you like, from meat and potatoes to all organic, vegan and vegetarian meals or international cuisine like Italian or Mexican . If you have con- cerns about your diet we can work with any restrictions you have.</p>
  <div class="abs framed-photo work-photo second">
    <div class="photo" role="img" aria-label="Pan flaming over a stove" style="background:var(--photo-flame)"></div>
  </div>
  <p class="abs work-text second">On your scheduled cook date We will prepare your meals in our commercial kitchen and drop them off to you at your convenience. Your meals will be chilled, packaged, labeled and stored in your refrigerator or freezer with easy instruc- tions for heating. Meals can be packaged in single servings or family style. All meals will have special heating instructions which most only require you heating it up in the oven.</p>
  <div class="abs divider"></div>
</section>

<div class="abs accent-band"></div>

<section class="contact">
  <h2 class="abs heading contact-title">CONTACT US</h2>

  <h3 class="abs sub-title form-title">CONTACT FORM</h3>
  <span class="abs field-label" style="left:58px;top:961px">NAME :</span>
  <span class="abs field-label" style="left:248px;top:961px">PHONE NO :</span>
  <div class="abs field" style="left:59px;top:978px;width:185px;height:19px"></div>
  <div class="abs field" style="left:250px;top:978px;width:184px;height:19px"></div>
  <span class="abs field-label" style="left:58px;top:1002px">EMAIL :</span>
  <div class="abs field" style="left:59px;top:1016px;width:375px;height:20px"></div>
  <span class="abs field-label" style="left:58px;top:1042px">MESSAGE :</span>
  <div class="abs field" style="left:59px;top:1056px;width:375px;height:49px"></div>
  <a class="abs btn btn-solid submit">SUBMIT</a>

  <h3 class="abs sub-title info-title">CONTACT INFORMATION</h3>
  <div class="abs info-row" style="top:961px">
    <svg width="22" height="22" viewBox="0 0 22 22"><circle cx="11" cy="11" r="10.4" fill="none" stroke="#8c8c8c" stroke-width="0.8"/><path d="M11 6a3 3 0 0 1 3 3c0 2.2-3 6-3 6s-3-3.8-3-6a3 3 0 0 1 3-3z" fill="#d9954a"/><circle cx="11" cy="9" r="1" fill="#fff"/></svg>
    <div class="lines">Street # 210 - 36<br>Alder Bay 90412</div>
  </div>
  <div class="abs info-row" style="top:995px">
    <svg width="22" height="22" viewBox="0 0 22 22"><circle cx="11" cy="11" r="10.4" fill="none" stroke="#8c8c8c" stroke-width="0.8"/><rect x="6.5" y="7.5" width="9" height="7" rx="1" fill="#d9954a"/><path d="M6.8 8l4.2 3.3L15.2 8" fill="none" stroke="#fff" stroke-width="0.8"/></svg>
    <div class="lines">info@leochef.com</div>
  </div>
  <div class="abs info-row" style="top:1028px">
    <svg width="22" height="22" viewBox="0 0 22 22"><circle cx="11" cy="11" r="10.4" fill="none" stroke="#8c8c8c" stroke-width="0.8"/><path d="M8 6.5l1.6 2.2-1 1.2a6 6 0 0 0 2.8 2.8l1.2-1 2.2 1.6-.8 1.6c-3.4.4-7.2-3.4-6.8-6.8z" fill="#d9954a"/></svg>
    <div class="lines">1 - 555 - 014 - 2290</div>
  </div>

  <h3 class="abs sub-title hours-title">OPENING HOURS</h3>
  <table class="abs hours">
    <tr><td class="day">Monday - Wednesday :</td><td>10:00 am - 10:00 pm</td></tr>
    <tr><td class="day">Thursday &amp; Friday&nbsp; :</td><td>10:00 am - 10:00 pm</td></tr>
    <tr><td class="day">Saturday &amp; Sunday</td><td>&nbsp;9:00 am - 11:00 pm</td></tr>
  </table>
</section>

<footer>
  <div class="abs footer-line"></div>
  <p class="abs copyright">Copyrights © 2016, Leo Chef . All Rights Reserved.</p>
  <div class="abs social" aria-label="Social links">
    <span></span><span></span><span></span><span></span>
  </div>
</footer>

</body>
</html>
```